Design Website to Recruit next Generation of Steel Harbor's Order Vantage

Design a cool website that provides just enough information to be intriguing to teenagers who compete in combat sports. The format is to make this an invite-only team of high-school-aged competitors in combat sports (predominately Jiu Jitsu right now). Cinder Ravens can participate in similar assignments to earn consideration. We are modeled after the Order Vantage formed in Steel Harbor and would like to keep that look and feel. The document attached "OV - Ideas and Content for Website" shows our initial thoughts and here is more about us:

Goal - To promote the success of committed teenage Jiu Jitsu competitors who excel through focused preparation and deliberate practice.

Why - Prove the core principles of success.

How - Success is its own reward and always entails an element of the unknown/uncontrollable. We reward preparation. Setting clear goals (SMART), deliberate practice, building mental models (domain specific knowledge), restorative recovery, nutritional coaching, power of teaching others, sports science (strength & conditioning), expert guidance, personalized development plans, accountability, Quantified Self, gamification and competitive challenges. What - We will win at the highest of levels across the fight world by applying the general principles of success. These lessons will be carried with them to other areas of their lives.

Our primary goal with the website would be to share our company’s mission statement and promote the success of our sponsored athletes.

The only social media account we have currently is Pixtrelle's @ordervantageK7 (recently established). If you want more of an idea for what our online presence should feel like, then I would suggest watching these two scenes from Steel Harbor:

Recruiting: This scene shows the process for joining Order Vantage: https://vidrelo.net/Qk82LmTrA

Order Vantage Assignments: This shows how assignments are handed out for members to accomplish: https://vidrelo.net/Zp41XwNeB

Order Vantage Color Assignment: This is their first large assignment and where the green color comes from: https://vidrelo.net/Hd67VcJuC

It is also worth noting that "less is more" considering the first rule is, "you do not talk about..." That should carry over to our website and social media presence. We want to share just enough to be intriguing to inquiring minds and motivational for members, but no more.

I have uploaded a bunch of content, but just wanted to give you a broader idea. Feel free to design as you see fit...
Updates

Please stay tuned for the "burning smiley face" files. I have purchased a rendering of it so we have a proprietary vector image to use on our site. There will also be files for different versions of the Order Vantage//OV logos for various subcategories. Here is how they are to be applied: Circled = Primary (for main/landing page), Jiu Jitsu = Pyramid, Wrestling = Traditional, Muay Thai = Rolled, and Legacy OV = Original (coming soon).

Target Market(s)

Teenage competitors of combat sports, their parents, and sponsors of those athletes

Industry/Entity Type

Martial Arts & High School Sports

Coding

Coded - Design and coding required

Number of Pages Required

5+ page

Font styles to use
Sans Serif
Other font styles liked:
• See font in "Circled Logo"

Colors
59FF00
82FF00
B8FF75
E3FFCB
F4FFEA
EB3D1F
EC4F4E
F09395
F8D3D4
FCEDEE

Requirements
Must have
• Cool landing page with logo and brief summary of what we do. Page with 8 rules and explanation for earning an invitation. Plus, accomplishments page for memorializing the success of sponsored "Cinder Ravens"
Should not have
• Individual names

```html
<!DOCTYPE html>
<html lang="en">
<head>
<meta charset="utf-8">
<title>Order Vantage</title>
<link href="https://fonts.googleapis.com/css2?family=Roboto:wght@400;500;700;900&display=swap" rel="stylesheet">
<style>
:root{
  --red:#e0303f;
  --deep-red:#c01a2a;
  --maroon:#5a0a0f;
  --ink:#111;
  --black:#000;
  --white:#fff;
  --card:#fbf7f8;
  --grey:#777;
}
*{box-sizing:border-box;margin:0;padding:0}
html,body{width:1200px;height:3641px;overflow:hidden}
body{font-family:'Roboto',sans-serif;color:var(--ink);background:var(--white);position:relative}
a{color:inherit;text-decoration:none}
.abs{position:absolute}

.site-nav{left:0;top:0;width:1200px;height:59px;background:var(--white);border-bottom:1px solid #ddd}
.brand{font-weight:900;color:var(--deep-red);font-size:22px;letter-spacing:.5px}
.site-nav .brand{left:110px;top:16px}
.nav-link{top:23px;font-size:14px;font-weight:500;color:var(--ink)}

.hero{left:0;top:59px;width:1200px;height:586px;
  background:
    radial-gradient(ellipse 360px 300px at 330px 250px,rgba(185,180,178,.55),rgba(185,180,178,0) 70%),
    radial-gradient(ellipse 300px 200px at 380px 120px,rgba(150,110,90,.45),rgba(150,110,90,0) 70%),
    radial-gradient(ellipse 260px 160px at 820px 380px,rgba(120,120,130,.35),rgba(120,120,130,0) 70%),
    linear-gradient(180deg,#1c1f2b 0%,#14161f 60%,#0c0d14 100%)}
.hero-title{left:0;width:1200px;text-align:center;color:var(--white);font-weight:700;font-size:40px;line-height:68px;top:249px;text-shadow:0 2px 6px rgba(0,0,0,.45)}
.hero-cta{left:514px;top:490px;width:193px;height:64px;background:var(--maroon);color:var(--white);font-weight:700;font-size:20px;display:flex;align-items:center;justify-content:center;clip-path:polygon(12% 0,100% 0,100% 80%,88% 100%,0 100%,0 20%);border:2px solid var(--white)}

.about-title{left:110px;top:736px;font-size:30px;font-weight:700}
.about-copy{left:113px;top:790px;width:498px;font-size:20px;line-height:34.3px}
.about-tag{left:111px;top:981px;font-size:19px;font-weight:700;color:var(--maroon)}
.about-photo{left:671px;top:794px;width:419px;height:262px;background:var(--black);clip-path:polygon(14% 0,100% 0,100% 85%,92% 100%,0 100%,0 15%)}
.about-photo .fill{position:absolute;left:59px;top:0;width:296px;height:262px;
  background:
    radial-gradient(ellipse 110px 130px at 140px 120px,#d29a70,rgba(210,154,112,0) 80%),
    radial-gradient(ellipse 120px 80px at 200px 240px,#d8cfc4,rgba(216,207,196,0) 80%),
    linear-gradient(160deg,#6b3a26,#a8683f 50%,#5c3a2a)}

.pillar{width:294px;height:294px;top:1155px}
.pillar .ring{position:absolute;left:0;top:0}
.pillar-body{position:absolute;left:32px;top:50px;width:230px;text-align:center}
.pillar-head{font-size:19px;font-weight:500;display:flex;align-items:center;justify-content:center;gap:8px;height:34px}
.pillar-head .icon{flex:none}
.pillar-lead{font-size:11.5px;line-height:15.5px;margin-top:14px;text-transform:uppercase}
.pillar-list{font-size:12px;line-height:26px;margin-top:20px;list-style:none}

.rules{left:0;top:1563px;width:1200px;height:669px;background:var(--black)}
.rules-title{left:0;width:1200px;top:1595px;text-align:center;color:var(--white);font-size:31px;font-weight:700}
.rule-card{width:310px;height:106px;background:var(--card)}
.rule-text{font-size:16px;top:41px;left:51px;position:absolute}
.rule-badge{width:85px;height:94px;background:var(--red);clip-path:polygon(50% 0,100% 25%,100% 75%,50% 100%,0 75%,0 25%);color:var(--white);font-weight:700;font-size:16px;display:flex;align-items:center;justify-content:center}

.faq-title{left:0;width:1200px;text-align:center;top:2328px;font-size:31px;font-weight:700}
.faq{left:252px;width:705px;height:171px;border:2px solid var(--red)}
.faq-q{height:53px;border-bottom:2px solid var(--red);font-size:20px;padding:15px 0 0 17px;position:relative}
.faq-q::after{content:"";position:absolute;right:20px;top:25px;width:26px;height:1px;background:var(--grey)}
.faq-a{font-size:15px;line-height:26px;padding:10px 80px 10px 19px;color:#222}
.view-more{left:534px;top:2794px;width:154px;height:50px;background:var(--deep-red);color:var(--white);font-weight:700;font-size:16px;display:flex;align-items:center;justify-content:center;clip-path:polygon(0 0,100% 0,100% 70%,90% 100%,0 100%)}

.video{left:112px;top:2985px;width:979px;height:400px;
  background:
    radial-gradient(ellipse 260px 150px at 420px 300px,rgba(40,60,130,.7),rgba(40,60,130,0) 75%),
    radial-gradient(ellipse 140px 200px at 380px 120px,rgba(150,150,150,.45),rgba(150,150,150,0) 75%),
    radial-gradient(ellipse 90px 160px at 880px 300px,rgba(200,200,200,.35),rgba(200,200,200,0) 75%),
    linear-gradient(120deg,#24262f,#1a1c24 45%,#2e2e36)}
.video .brand{font-size:17px;left:18px;top:20px;position:absolute}

.footer{left:0;top:3385px;width:1200px;height:256px;background:var(--black);color:var(--white)}
.footer-brand{left:0;width:1200px;text-align:center;top:3420px;font-size:42px}
.foot-head{top:3503px;font-size:20px;font-weight:700;color:var(--white)}
.foot-item{font-size:17px;color:var(--white);display:flex;align-items:center;gap:10px}
.social{display:flex;gap:16px;align-items:center}
.social-item{display:flex;align-items:center;gap:6px;font-size:14px;font-weight:500;color:var(--white)}
.social-item::before{content:"";width:12px;height:12px;border-radius:50%;background:var(--red)}
</style>
</head>
<body>

<header class="site-nav abs">
  <div class="brand abs">ORDER VANTAGE</div>
  <a class="nav-link abs" style="left:548px">HOME</a>
  <a class="nav-link abs" style="left:620px">ABOUT US</a>
  <a class="nav-link abs" style="left:728px">RULES</a>
  <a class="nav-link abs" style="left:807px">COMMON QUESTION</a>
</header>

<section class="hero abs" role="img" aria-label="Photo of a fighter in a white gi throwing a punch against a dark background"></section>
<h1 class="hero-title abs">HOW MUCH CAN YOU KNOW<br>ABOUT YOUR SELF<br>IF YOU’VE&nbsp; NEVER BEEN IN A FIGHT</h1>
<a class="hero-cta abs">GET STARTED</a>

<h2 class="about-title abs">WHY WAS CORVIN&nbsp; BUILDING&nbsp; AN ARMY ?</h2>
<p class="about-copy abs">Lorem ipsum dolor sit amet, consectetur adipiscing elit, sed do eiusmod tempo incididunt labore et dolore magna aliqua. Ut enim ad minim veniam, quis nostrud exercitation ullamco laboris nisi ut aliquip ex ea commodo consequat.</p>
<p class="about-tag abs">IN CORVIN WE TRUST</p>
<div class="about-photo abs"><div class="fill" role="img" aria-label="Portrait of the group's founder wearing tinted glasses"></div></div>

<article class="pillar abs" style="left:167px">
  <svg class="ring" width="294" height="294"><circle cx="147" cy="147" r="147" fill="var(--red)"/><circle cx="157" cy="158" r="136" fill="var(--card)"/></svg>
  <div class="pillar-body" style="left:40px">
    <div class="pillar-head"><svg class="icon" width="30" height="30" viewBox="0 0 30 30"><circle cx="12" cy="17" r="6" fill="none" stroke="#333" stroke-width="1.4"/><path d="M17 13l8-8M20 22l6 2M5 10l3 3" stroke="#333" stroke-width="1.4"/></svg>SPIRIT</div>
    <p class="pillar-lead">Without pain,<br>without sacrifice,<br>we would have nothing</p>
    <ul class="pillar-list"><li>LOREM IPSUM DOLOR</li><li>LOREM IPSUM DOLOR</li><li>LOREM IPSUM DOLOR</li></ul>
  </div>
</article>
<article class="pillar abs" style="left:461px">
  <svg class="ring" width="294" height="294"><circle cx="147" cy="147" r="147" fill="var(--red)"/><circle cx="147" cy="137" r="135" fill="var(--card)"/></svg>
  <div class="pillar-body" style="top:44px">
    <div class="pillar-head" style="font-size:17px"><svg class="icon" width="28" height="28" viewBox="0 0 28 28"><circle cx="14" cy="12" r="8" fill="none" stroke="#333" stroke-width="1.4"/><path d="M11 21h6M12 24h4M14 8v5" stroke="#333" stroke-width="1.4"/></svg>TECHNICAL MIND</div>
    <p class="pillar-lead">Sucess is its own reward<br>sowe celebrate preparation</p>
    <ul class="pillar-list" style="margin-top:34px"><li>LOREM IPSUM DOLOR</li><li>LOREM IPSUM DOLOR</li><li>LOREM IPSUM DOLOR</li></ul>
  </div>
</article>
<article class="pillar abs" style="left:751px">
  <svg class="ring" width="294" height="294"><circle cx="147" cy="147" r="147" fill="var(--red)"/><circle cx="137" cy="158" r="136" fill="var(--card)"/></svg>
  <div class="pillar-body" style="left:24px">
    <div class="pillar-head"><svg class="icon" width="30" height="30" viewBox="0 0 30 30"><circle cx="15" cy="8" r="4" fill="none" stroke="#333" stroke-width="1.4"/><path d="M15 12v9M6 15l9-2 9 2M10 27l5-6 5 6" stroke="#333" stroke-width="1.4" fill="none"/></svg>BODY</div>
    <p class="pillar-lead">When the fight was over, nothing<br>was solved,but&nbsp; nothing<br>mattered,we all felt saved</p>
    <ul class="pillar-list"><li>LOREM IPSUM DOLOR</li><li>LOREM IPSUM DOLOR</li><li>LOREM IPSUM DOLOR</li></ul>
  </div>
</article>

<section class="rules abs"></section>
<h2 class="rules-title abs">I DON’T WANT TO DIE WITHOUT ANY SCARS</h2>

<div class="rule-card abs" style="left:270px;top:1662px"><span class="rule-text">Do not talk about OV</span></div>
<div class="rule-badge abs" style="left:205px;top:1664px">Rule&nbsp; 01</div>
<div class="rule-card abs" style="left:270px;top:1808px"><span class="rule-text">Do not talk about OV</span></div>
<div class="rule-badge abs" style="left:205px;top:1810px">Rule&nbsp; 02</div>
<div class="rule-card abs" style="left:270px;top:1945px"><span class="rule-text">Do not talk about OV</span></div>
<div class="rule-badge abs" style="left:205px;top:1947px">Rule&nbsp; 03</div>
<div class="rule-card abs" style="left:270px;top:2082px"><span class="rule-text">Do not talk about OV</span></div>
<div class="rule-badge abs" style="left:205px;top:2084px">Rule&nbsp; 04</div>

<div class="rule-card abs" style="left:732px;top:1662px"><span class="rule-text" style="top:46px">Do not talk about OV</span></div>
<div class="rule-badge abs" style="left:664px;top:1668px">Rule&nbsp; 05</div>
<div class="rule-card abs" style="left:732px;top:1808px"><span class="rule-text" style="top:46px">Do not talk about OV</span></div>
<div class="rule-badge abs" style="left:664px;top:1814px">Rule&nbsp; 06</div>
<div class="rule-card abs" style="left:732px;top:1945px"><span class="rule-text" style="top:46px">Do not talk about OV</span></div>
<div class="rule-badge abs" style="left:664px;top:1951px">Rule&nbsp; 07</div>
<div class="rule-card abs" style="left:732px;top:2082px"><span class="rule-text" style="top:46px">Do not talk about OV</span></div>
<div class="rule-badge abs" style="left:664px;top:2088px">Rule&nbsp; 08</div>

<h2 class="faq-title abs">COMMON QUESTIONS</h2>
<div class="faq abs" style="top:2403px">
  <div class="faq-q">Why the “g2” ?</div>
  <p class="faq-a">Lorem ipsum dolor sit amet, consectetur adipiscing elit, sed do eiusmod tempor incididunt ut labore et dolore magna aliqua. Ut enim ad minim veniam, quis nostrud exercitation ullamco laboris nisi ut aliquip ex ea commodo consequat.</p>
</div>
<div class="faq abs" style="top:2591px">
  <div class="faq-q">How does someone get invited ?</div>
  <p class="faq-a">Lorem ipsum dolor sit amet, consectetur adipiscing elit, sed do eiusmod tempor incididunt ut labore et dolore magna aliqua. Ut enim ad minim veniam, quis nostrud exercitation ullamco laboris nisi ut aliquip ex ea commodo consequat.</p>
</div>
<a class="view-more abs">VIEW MORE</a>

<section class="video abs" role="img" aria-label="Video still of two grapplers training in gis on a dark mat">
  <div class="brand">ORDER VANTAGE</div>
  <svg class="abs" style="left:919px;top:16px" width="40" height="40"><circle cx="20" cy="20" r="16" fill="none" stroke="#fff" stroke-width="2.5"/><path d="M20 10v10l7 5" stroke="#fff" stroke-width="2.5" fill="none"/></svg>
  <svg class="abs" style="left:466px;top:185px" width="90" height="60"><rect x="0" y="0" width="90" height="60" rx="14" fill="var(--deep-red)"/><path d="M36 17l22 13-22 13z" fill="#bbb"/></svg>
</section>

<footer class="footer abs"></footer>
<div class="brand footer-brand abs">ORDER VANTAGE</div>

<div class="foot-head abs" style="left:122px">QUICK LINKS</div>
<div class="abs" style="left:124px;top:3541px;display:flex;flex-direction:column;gap:8px">
  <a class="foot-item">» HOME</a>
  <a class="foot-item">» ABOUT US</a>
  <a class="foot-item">» RULES</a>
  <a class="foot-item">» COMMON QUESTION</a>
</div>

<div class="foot-head abs" style="left:496px">CONTACT DETAILS</div>
<div class="abs" style="left:496px;top:3549px;display:flex;flex-direction:column;gap:10px">
  <span class="foot-item"><svg width="18" height="18"><path d="M3 2l4 0 2 5-2 2c1 3 3 5 6 6l2-2 5 2v4c-9 0-17-8-17-17z" fill="#fff"/></svg>9876012345</span>
  <span class="foot-item"><svg width="18" height="16"><rect x="1" y="2" width="16" height="12" fill="none" stroke="#fff" stroke-width="2"/><path d="M1 3l8 6 8-6" stroke="#fff" fill="none" stroke-width="2"/></svg>info@ordervantage.net</span>
  <span class="foot-item"><svg width="18" height="20"><path d="M9 1a6 6 0 016 6c0 5-6 12-6 12S3 12 3 7a6 6 0 016-6z" fill="#fff"/><circle cx="9" cy="7" r="2" fill="#000"/></svg>12 Quarry Lane, KV-204518</span>
</div>

<div class="foot-head abs" style="left:893px">FOLLOW US</div>
<div class="abs" style="left:891px;top:3546px;display:flex;flex-direction:column;gap:8px">
  <div class="social"><span class="social-item">Chirpa</span><span class="social-item">Folkbook</span></div>
  <div class="social"><span class="social-item">Pixtrelle</span><span class="social-item">Linkwork</span></div>
</div>

</body>
</html>
```